Looking to build a senior life alert web page

We definitely want to incorporate pictures of the product in which we're selling and want colors that resonate with the senior community. We're looking for something also clean and very easy to navigate. We're looking to pick a design immediately!
Based on something similar to that of our competition which can be located at the following
https://www.tovrelcarelink.example/
https://www.wellkestrix.example/

attached is the product we're selling

The name of our company is the golden harbor circle

Target Market(s)

Elderly people looking for a life alert device

Industry/Entity Type

Medical Equipment

Number of Pages Required

3 page

Font styles to use
Serif

Colors

Designer to choose colors to be used in the design.

Requirements
Must have
• Pictures of the product a nice UI experience that can be easily made mobile friendly
Nice to have
• Including area for video content maybe / friendly color LOGOS are attached for our company

```html
<!DOCTYPE html>
<html lang="en">
<head>
<meta charset="utf-8">
<title>Golden Harbor Circle</title>
<link rel="stylesheet" href="https://fonts.googleapis.com/css2?family=Lato:wght@400;700;900&display=swap">
<style>
:root{
  --orange:#e8862a;
  --navy:#1f4d80;
  --navy-dark:#173a63;
  --ink:#2b2b2b;
  --muted:#666;
  --light:#f2f2f2;
  --gray:#e6e6e6;
  --footer:#3a3d42;
  --white:#fff;
}
*{box-sizing:border-box;margin:0;padding:0}
html,body{width:1200px;height:3352px;overflow:hidden}
body{font-family:"Lato",Arial,sans-serif;color:var(--ink);background:var(--white)}
.section{position:relative;width:1200px}
.btn{display:inline-block;font-weight:700;font-size:18px;letter-spacing:.5px;padding:14px 28px;text-decoration:none}
.btn-solid{background:var(--orange);color:var(--white)}
.btn-outline{border:2px solid var(--navy);color:var(--navy);background:transparent}
.heading{font-weight:700;color:var(--orange);font-size:32px;letter-spacing:.3px}
p{font-size:14.5px;line-height:26px;color:var(--muted)}

/* header */
.site-header{height:100px;display:flex;align-items:center;padding:0 98px;justify-content:space-between;background:var(--white)}
.brand{display:flex;align-items:center;gap:10px;font-weight:700;font-size:17px;color:var(--ink)}
.brand-dot{width:26px;height:26px;border-radius:50%;background:var(--orange)}
.main-nav{display:flex;align-items:center;gap:30px;font-size:14.5px}
.main-nav a{color:var(--ink);text-decoration:none}
.main-nav a.active{color:var(--orange);border-bottom:2px solid var(--orange);padding-bottom:4px}
.phone{display:flex;align-items:center;gap:8px;font-size:19px;margin-left:10px}
.cart{display:flex;align-items:center;gap:4px;font-size:13px}

/* hero */
.hero{height:605px;background:linear-gradient(180deg,#8a7a68 0%,#5e5347 60%,#4b4239 100%);text-align:center;overflow:hidden}
.hero-photo{position:absolute;inset:0;background:radial-gradient(ellipse at 50% 30%,#b7aa99 0%,#7c6e5f 45%,#4a4037 100%)}
.hero-device{position:absolute;left:395px;top:0;width:170px;height:230px;border-radius:12px;background:linear-gradient(160deg,#e9e5df,#c9c3bb)}
.hero-content{position:absolute;top:240px;left:0;right:0}
.hero-title{font-weight:900;font-size:50px;color:var(--white);letter-spacing:1px}
.hero-sub{color:#f1ece6;font-size:14px;margin:6px 0 24px}
.hero-arrow{position:absolute;top:282px;width:44px;height:44px;border-radius:50%;background:rgba(0,0,0,.25)}

/* about */
.about{height:455px}
.about-text{position:absolute;left:100px;top:80px;width:555px}
.about-text p{margin-top:18px}
.about-text .btn{margin-top:22px;padding:11px 24px}
.frame{position:absolute;background:var(--white);border:1px solid #ddd;padding:8px;box-shadow:0 1px 3px rgba(0,0,0,.08)}
.about .frame{left:695px;top:80px;width:410px;height:305px}
.photo{width:100%;height:100%}

/* products */
.products{height:575px;background:var(--light);text-align:center}
.products .heading{padding-top:60px}
.products .lead{color:var(--ink);font-size:15px;margin-top:6px}
.product-grid{position:absolute;top:182px;left:100px;display:flex;gap:24px}
.product{width:232px}
.product-card{height:218px;background:var(--white);display:flex;align-items:center;justify-content:center}
.product-img{width:95px;height:150px;border-radius:14px;background:linear-gradient(160deg,#f4f4f4,#cfcfcf)}
.product h3{font-weight:400;font-size:18px;margin-top:28px;color:var(--ink)}
.product p{font-size:13.5px;line-height:19px;margin-top:6px}

/* benefits */
.benefits{height:465px;background:linear-gradient(135deg,var(--navy) 0%,#2d5f95 60%,var(--navy-dark) 100%);text-align:center;color:var(--white)}
.benefits h2{font-weight:700;font-size:36px;padding-top:72px}
.benefits p{color:#e8eef6;font-size:13px;line-height:26px;width:1000px;margin:18px auto 0}
.benefits .btn{margin-top:28px;padding:11px 26px}

/* reviews */
.reviews{height:340px;background:var(--gray);text-align:center}
.reviews .heading{padding-top:52px;font-size:36px}
.quote-title{font-size:19px;margin-top:18px;color:var(--ink)}
.quote-body{font-size:13px;line-height:22px;color:var(--ink);width:930px;margin:4px auto 0}
.reviewer{display:flex;align-items:center;justify-content:center;gap:14px;margin-top:16px}
.avatar{width:58px;height:58px;border-radius:50%;background:linear-gradient(135deg,#c8b9a6,#8e7f6d)}
.reviewer-name{font-size:20px;font-weight:700;text-align:left}
.stars{display:flex;gap:3px;margin-top:3px}
.rev-arrow{position:absolute;top:160px}

/* video */
.video{height:470px}
.video-text{position:absolute;left:100px;top:72px;width:525px}
.video-text p{margin-top:20px}
.video .frame{left:660px;top:65px;width:445px;height:295px}
.play{position:absolute;left:50%;top:50%;transform:translate(-50%,-50%)}

/* footer */
.site-footer{height:342px;background:var(--footer);color:var(--white)}
.footer-title{font-weight:700;font-size:17px}
.quick{position:absolute;left:100px;top:48px}
.quick-cols{display:flex;gap:95px;margin-top:18px}
.quick-cols ul{list-style:none;font-size:14.5px;line-height:32px}
.footer-device{position:absolute;left:540px;top:60px;width:80px;height:115px;border-radius:10px;background:linear-gradient(160deg,#eee,#bbb)}
.newsletter{position:absolute;left:775px;top:48px;width:330px}
.newsletter .small{font-size:14px;margin-top:12px}
.signup{display:flex;margin-top:14px}
.signup .field{flex:1;height:38px;background:var(--white);color:#aaa;font-size:11px;padding:12px 14px}
.signup .go{background:var(--orange);font-weight:700;font-size:13px;padding:12px 16px}
.socials{display:flex;gap:14px;margin-top:18px}
.social{width:38px;height:38px;border-radius:50%;background:var(--orange)}
.footer-bottom{position:absolute;left:100px;right:100px;top:280px;border-top:1px solid #5a5d63;padding-top:18px;display:flex;justify-content:space-between;font-size:12px;color:#b8b8b8}
.pay{display:flex;gap:8px;align-items:center}
.pay span{width:34px;height:14px;background:#8a8d92;border-radius:2px}
</style>
</head>
<body>

<header class="section site-header">
  <div class="brand"><span class="brand-dot"></span>Golden Harbor Circle</div>
  <nav class="main-nav">
    <a class="active" href="#">Home</a>
    <a href="#">About Us</a>
    <a href="#">Our Products &#709;</a>
    <a href="#">Videos</a>
    <a href="#">Review</a>
    <a href="#">Contact Us</a>
    <span class="phone">
      <svg width="14" height="14" viewBox="0 0 24 24"><path fill="#e8862a" d="M6.6 10.8a15 15 0 006.6 6.6l2.2-2.2c.3-.3.7-.4 1-.2 1.1.4 2.3.6 3.6.6.6 0 1 .4 1 1V20c0 .6-.4 1-1 1A17 17 0 013 4c0-.6.4-1 1-1h3.5c.6 0 1 .4 1 1 0 1.3.2 2.5.6 3.6.1.3 0 .7-.2 1z"/></svg>
      1-800-555-0142</span>
    <span class="cart">
      <svg width="24" height="22" viewBox="0 0 24 22"><path fill="#2b2b2b" d="M0 1h4l3 12h13l3-9H7" stroke="#2b2b2b" stroke-width="2" fill-opacity="0"/><circle cx="9" cy="18" r="2" fill="#2b2b2b"/><circle cx="18" cy="18" r="2" fill="#2b2b2b"/></svg>(0)
    </span>
  </nav>
</header>

<section class="section hero">
  <div class="hero-photo" role="img" aria-label="Hand holding up the white emergency alert pendant against a softly blurred home interior"></div>
  <div class="hero-device" role="img" aria-label="Emergency alert device"></div>
  <div class="hero-arrow" style="left:22px"></div>
  <div class="hero-arrow" style="right:22px"></div>
  <div class="hero-content">
    <h1 class="hero-title">GOLDEN HARBOR CIRCLE</h1>
    <div class="hero-sub">Ut enim ad minima veniam, quis nostrum exercitationem ullam corporis suscipit laboriosam</div>
    <a class="btn btn-solid" href="#">LEARN MORE</a>
  </div>
</section>

<section class="section about">
  <div class="about-text">
    <h2 class="heading" style="font-size:29px">ABOUT GOLDEN HARBOR CIRCLE</h2>
    <p>Sed ut perspiciatis unde omnis iste natus error sit voluptatem accusantium doloremque laudantium, totam rem aperiam, eaque ipsa quae ab illo inventore veritatis et quasi architecto beatae vitae dicta sunt explicabo. Nemo enim ipsam voluptatem quia voluptas sit aspernatur aut odit aut fugit.</p>
    <p>Neque porro quisquam est, qui dolorem ipsum quia dolor sit amet, consectetur, adipisci velit, sed quia non numquam eius modi tempora incidunt ut labore et dolore magnam.</p>
    <a class="btn btn-outline" href="#">LEARN MORE</a>
  </div>
  <div class="frame"><div class="photo" role="img" aria-label="Senior couple sitting together at a laptop at home" style="background:linear-gradient(135deg,#d9cdbd,#8d8a86 55%,#3e4a6a)"></div></div>
</section>

<section class="section products">
  <h2 class="heading" style="font-size:36px">OUR PRODUCTS</h2>
  <div class="lead">Quis autem vel eum iure reprehenderit qui in ea voluptate velit esse</div>
  <div class="product-grid">
    <div class="product"><div class="product-card"><div class="product-img" role="img" aria-label="Emergency alert pendant, front view"></div></div><h3>DUCIMUS QUI BLANDITII</h3><p>Similique sunt in culpa qui officia deserunt mollitia animi...</p></div>
    <div class="product"><div class="product-card"><div class="product-img" role="img" aria-label="Emergency alert base unit"></div></div><h3>ARCHITECTO BEATAE</h3><p>Natus error sit voluptatem accusan&shy;tium doloremque...</p></div>
    <div class="product"><div class="product-card"><div class="product-img" role="img" aria-label="Emergency alert pendant, angled view"></div></div><h3>INVENTORE VERITATIS ET</h3><p>Consequuntur magni dolores eos qui ratione voluptatem sequi...</p></div>
    <div class="product"><div class="product-card"><div class="product-img" role="img" aria-label="Emergency alert pendant with lanyard"></div></div><h3>MAGNAM ALIQUAM QUA</h3><p>Vel illum qui dolorem eum fugiat quo voluptas nulla...</p></div>
  </div>
</section>

<section class="section benefits" role="img" aria-label="Blue tinted background of a keyboard with hands">
  <h2>GOLDEN HARBOR CIRCLE BENEFITS</h2>
  <p>At vero eos et accusamus et iusto odio dignissimos ducimus qui blanditiis praesentium voluptatum deleniti atque corrupti quos dolores et quas molestias excepturi sint occaecati cupiditate non provident, similique sunt in culpa qui officia deserunt mollitia animi, id est laborum et dolorum fuga. Et harum quidem rerum facilis est et expedita distinctio.</p>
  <p>Nam libero tempore, cum soluta nobis est eligendi optio cumque nihil impedit quo minus id quod maxime placeat facere possimus, omnis voluptas assumenda est, omnis dolor repellendus. Temporibus autem quibusdam et aut officiis debitis aut rerum necessitatibus saepe eveniet ut et voluptates repudiandae sint et molestiae non recusandae. Itaque earum rerum hic tenetur a sapiente delectus.</p>
  <a class="btn btn-solid" href="#">LEARN MORE</a>
</section>

<section class="section reviews">
  <h2 class="heading">CUSTOMER REVIEWS</h2>
  <div class="quote-title"><span style="color:#999;font-size:26px">&ldquo;</span> Pellentesque convallis molestie enim sit amet efficitur amet consequat risus.</div>
  <div class="quote-body">Nullam accumsan purus vel tempus viverra. Mauris suscipit felis id nunc elementum varius. Praesent elementum nulla sit amet justo pellentesque scelerisque. Nam et tortor in ante iaculis porttitor in luctus mi. Vivamus gravida sem a pretium euismod. <span style="color:#999;font-size:26px">&rdquo;</span></div>
  <div class="reviewer">
    <div class="avatar" role="img" aria-label="Reviewer portrait"></div>
    <div>
      <div class="reviewer-name">Ellen Marsh, City</div>
      <div class="stars">
        <svg width="100" height="18" viewBox="0 0 100 18"><g fill="#e8862a"><polygon points="9,0 11.5,6 18,6.5 13,10.8 14.6,17 9,13.6 3.4,17 5,10.8 0,6.5 6.5,6"/><polygon transform="translate(20)" points="9,0 11.5,6 18,6.5 13,10.8 14.6,17 9,13.6 3.4,17 5,10.8 0,6.5 6.5,6"/><polygon transform="translate(40)" points="9,0 11.5,6 18,6.5 13,10.8 14.6,17 9,13.6 3.4,17 5,10.8 0,6.5 6.5,6"/><polygon transform="translate(60)" points="9,0 11.5,6 18,6.5 13,10.8 14.6,17 9,13.6 3.4,17 5,10.8 0,6.5 6.5,6"/><polygon transform="translate(80)" points="9,0 11.5,6 18,6.5 13,10.8 14.6,17 9,13.6 3.4,17 5,10.8 0,6.5 6.5,6"/></g></svg>
      </div>
    </div>
  </div>
  <svg class="rev-arrow" style="left:98px" width="14" height="24" viewBox="0 0 14 24"><path d="M12 2L2 12l10 10" stroke="#777" stroke-width="2.5" fill="none"/></svg>
  <svg class="rev-arrow" style="right:98px" width="14" height="24" viewBox="0 0 14 24"><path d="M2 2l10 10L2 22" stroke="#777" stroke-width="2.5" fill="none"/></svg>
</section>

<section class="section video">
  <div class="video-text">
    <h2 class="heading">OUR VIDEO</h2>
    <p>On the other hand, we denounce with righteous indignation and dislike men who are so beguiled and demoralized by the charms of pleasure of the moment, so blinded by desire, that they cannot foresee the pain and trouble that are bound to ensue; and equal blame belongs to those who fail in their duty through weakness of will, which is the same as saying through shrinking from toil and pain. These cases are perfectly simple and easy to distinguish.</p>
    <p>Neque porro quisquam est, qui dolorem ipsum quia dolor sit amet, consectetur, adipisci velit, sed quia non numquam eius modi tempora incidunt ut labore et dolore magnam aliquam quaerat voluptatem.</p>
  </div>
  <div class="frame">
    <div class="photo" role="img" aria-label="Video still of a caregiver chatting with a senior woman in a bright living room" style="background:linear-gradient(135deg,#c9b8a8,#e6dcd0 45%,#a58f86)"></div>
    <svg class="play" width="70" height="70" viewBox="0 0 70 70"><circle cx="35" cy="35" r="32" fill="none" stroke="#fff" stroke-width="3"/><polygon points="28,22 50,35 28,48" fill="none" stroke="#fff" stroke-width="3"/></svg>
  </div>
</section>

<footer class="section site-footer">
  <div class="quick">
    <div class="footer-title">QUICK LINKS</div>
    <div class="quick-cols">
      <ul><li>Home</li><li>About Us</li><li>Our Products</li><li>Videos</li><li>Review</li></ul>
      <ul style="margin-top:4px"><li>Contact</li><li>Shop</li><li>Enquiry</li><li>FAQ</li></ul>
    </div>
  </div>
  <div class="footer-device" role="img" aria-label="Emergency alert pendant"></div>
  <div class="newsletter">
    <div class="footer-title">SIGN UP FOR NEWSLETTERS</div>
    <div class="small">Please sign up here for latest news</div>
    <div class="signup"><div class="field">EMAIL ADDRESS</div><div class="go">SUBSCRIBE</div></div>
    <div class="socials"><span class="social"></span><span class="social"></span><span class="social"></span><span class="social"></span></div>
  </div>
  <div class="footer-bottom">
    <span>&copy; 2017 Golden Harbor Circle. All right reserved. Term of Use</span>
    <span class="pay"><span></span><span></span><span></span><span></span><span></span></span>
  </div>
</footer>

</body>
</html>
```